Business Card Design for Marketing Firm

Looking for business card design for higher end marketing firm. Clean but impressionable/trendy. We are a marketing firm that represents manufacturers in the foodservice equipment and supply industry. Our customers are end users such has hotels, restaurants, country clubs, convention centers and casinos as well as distributors of restaurants supplies and equipment, and manufacturers of foodservice equipment and supplies.
Target Market(s)
Hotels, Restaurants, Supply & Equipment Distributors, Foodservice Manufacturers
Industry/Entity Type
Foodservice/Hospitality
Contact Information for Business Card
Name, Title, Contact Number, Email, Website, Social Media, Address
Requirements
Must have
- Clean & Simple but Serious and Impressionable

```html
<!DOCTYPE html>
<html lang="en">
<head>
<meta charset="utf-8">
<title>Meridian Service Reps – Business Card</title>
<link rel="stylesheet" href="https://fonts.googleapis.com/css2?family=Montserrat:wght@300;400;500;700&display=swap">
<style>
  :root {
    --stage: #2b2b2d;
    --brand-blue: #2e2d7a;
    --brand-blue-light: #3f3d8f;
    --brand-blue-dark: #1f1e63;
    --band-grey: #4a4a4c;
    --card-white: #f7f7f7;
    --card-white-shade: #e6e6e6;
    --ink-light: #ffffff;
  }
  * { box-sizing: border-box; margin: 0; padding: 0; }
  html, body { width: 1200px; height: 1200px; overflow: hidden; }
  body {
    background: var(--stage);
    font-family: "Montserrat", Arial, sans-serif;
    position: relative;
  }
  .card {
    position: absolute;
    left: 150px;
    width: 900px;
    height: 514px;
    overflow: hidden;
    background: linear-gradient(135deg, var(--card-white) 40%, var(--card-white-shade) 100%);
    box-shadow: 0 10px 30px rgba(0,0,0,.45);
  }
  .card--front { top: 60px; }
  .card--back { top: 626px; }

  .wordmark {
    position: absolute;
    color: var(--brand-blue);
    font-weight: 500;
    letter-spacing: .06em;
    text-transform: uppercase;
    text-align: right;
    line-height: 1.15;
    white-space: nowrap;
  }
  .card--front .wordmark { left: 0; right: 0; top: 205px; text-align: center; font-size: 40px; }
  .card--back .wordmark { right: 40px; top: 232px; font-size: 21px; }
  .wordmark__sub { display: block; font-size: .62em; letter-spacing: .14em; }

  .back-art { position: absolute; inset: 0; width: 900px; height: 514px; }

  .contact-panel {
    position: absolute;
    left: 56px;
    top: 50px;
    color: var(--ink-light);
  }
  .contact-panel__name { font-size: 34px; font-weight: 700; letter-spacing: .01em; }
  .contact-panel__title { font-size: 17px; font-weight: 300; margin-top: 4px; }
  .contact-panel__address { font-size: 17px; font-weight: 400; margin-top: 40px; line-height: 1.5; }
  .contact-list { list-style: none; margin-top: 10px; font-size: 17px; line-height: 1.6; }
  .contact-list li { display: flex; align-items: center; gap: 10px; }
  .contact-list svg { width: 15px; height: 15px; flex: none; }
</style>
</head>
<body>

<section class="card card--front" aria-label="Card front">
  <div class="wordmark">Meridian Service<span class="wordmark__sub">Reps</span></div>
</section>

<section class="card card--back" aria-label="Card back">
  <svg class="back-art" viewBox="0 0 900 514" aria-hidden="true">
    <defs>
      <linearGradient id="panelBlue" x1="0" y1="1" x2="1" y2="0">
        <stop offset="0" stop-color="var(--brand-blue-dark)"/>
        <stop offset="1" stop-color="var(--brand-blue-light)"/>
      </linearGradient>
    </defs>
    <path d="M0 0 H700 C575 110 512 300 505 514 H0 Z" fill="url(#panelBlue)"/>
    <path d="M0 0 H628 C530 110 482 300 478 514 H0 Z" fill="var(--band-grey)"/>
    <path d="M0 0 H612 C505 110 450 300 440 514 H0 Z" fill="url(#panelBlue)"/>
    <path d="M628 0 C530 110 482 300 478 514" fill="none" stroke="#fff" stroke-width="4"/>
    <path d="M612 0 C505 110 450 300 440 514" fill="none" stroke="#fff" stroke-width="4"/>
  </svg>

  <div class="contact-panel">
    <div class="contact-panel__name">Calder Vance</div>
    <div class="contact-panel__title">Founder &amp; Director</div>
    <div class="contact-panel__address">4518 Orchard Lane<br>Bayview Maine 11370</div>
    <ul class="contact-list">
      <li><svg viewBox="0 0 16 16"><path d="M3 1.5l3 .5 1 3-2 1.5a9 9 0 004.5 4.5L11 9l3 1 .5 3-2 1.5A12 12 0 011.5 3.5z" fill="#fff"/></svg>(405)-555-0147</li>
      <li><svg viewBox="0 0 16 16"><rect x="1" y="3" width="14" height="10" rx="1" fill="#fff"/><path d="M1.5 3.5 8 9l6.5-5.5" fill="none" stroke="var(--brand-blue)" stroke-width="1.4"/></svg>vance@meridianservicereps.com</li>
      <li><svg viewBox="0 0 16 16"><circle cx="8" cy="8" r="6.5" fill="none" stroke="#fff" stroke-width="1.4"/><ellipse cx="8" cy="8" rx="2.8" ry="6.5" fill="none" stroke="#fff" stroke-width="1.2"/><path d="M1.5 8h13" stroke="#fff" stroke-width="1.2"/></svg>www.meridianservicereps.com</li>
      <li><svg viewBox="0 0 16 16"><circle cx="8" cy="8" r="7" fill="#fff"/></svg>@meridianservicereps</li>
    </ul>
  </div>

  <div class="wordmark">Meridian Service<span class="wordmark__sub">Reps</span></div>
</section>

</body>
</html>
```